Business card design needed

We are a boutique law firm within the Melbourne CBD.

You will need to upload our company logo which is to go on the left hand side of the business card - we then have a Legal Guild of Tarrowmere logo to go perhaps on the bottom right hand side (color)

On the back we would like the website details

www.pendrakesolicitors.com.au - with a small logo
Updates

Thank you designers for all your great submissions.  Just going through the designs and we will choose one within the next couple of days.

Kind Regards
Pendrake Solicitors Pty Ltd

Industry/Entity Type

Boutique

Contact Information for Business Card

Darian Pendrake
Principal
Level 6, 47 Corlett Street
Melbourne VIC Australia 3000
T+61 3 9620 2088 F+61 3 9629 3938
darian@pendrakesolicitors.com.au
M 0491 570 226

```html
<!DOCTYPE html>
<html lang="en">
<head>
<meta charset="utf-8">
<title>Pendrake Solicitors – Business Card</title>
<link rel="stylesheet" href="https://fonts.googleapis.com/css2?family=Source+Sans+3:wght@300;700&display=swap">
<style>
  :root {
    --page: #ffffff;
    --card: #e04c27;
    --card-shade: #d63a26;
    --ink: #ffffff;
  }
  html, body {
    margin: 0;
    padding: 0;
    width: 1200px;
    height: 1000px;
    overflow: hidden;
    background: var(--page);
  }
  .canvas {
    position: relative;
    width: 1200px;
    height: 1000px;
    background: var(--page);
    font-family: "Source Sans 3", sans-serif;
  }
  .card {
    position: absolute;
    left: 79px;
    top: 202px;
    width: 1040px;
    height: 590px;
    background: var(--card);
    overflow: hidden;
  }
  .card__rule {
    position: absolute;
    left: 0;
    width: 100%;
    height: 13px;
    background: var(--ink);
  }
  .card__rule--top { top: 43px; }
  .card__rule--bottom { top: 535px; }
  .card__backdrop {
    position: absolute;
    left: 621px;
    top: 136px;
    width: 355px;
    height: 355px;
    background: var(--card-shade);
  }
  .brand {
    position: absolute;
    left: 244px;
    top: 56px;
    display: flex;
    align-items: flex-end;
    gap: 12px;
    height: 114px;
  }
  .brand__square {
    width: 114px;
    height: 114px;
    background: var(--ink);
  }
  .brand__name {
    color: var(--ink);
    font-family: "Source Sans 3", sans-serif;
    font-weight: 700;
    font-size: 60px;
    line-height: 1;
    margin-bottom: -6px;
  }
  .contact {
    position: absolute;
    left: 0;
    top: 0;
    width: 100%;
    height: 100%;
    margin: 0;
    color: var(--ink);
    font-weight: 300;
    font-size: 31px;
    letter-spacing: -0.6px;
  }
  .contact__line {
    position: absolute;
    left: 390px;
    transform: translateX(-50%);
    white-space: nowrap;
    line-height: 40px;
  }
  .contact__line--name { top: 218px; }
  .contact__line--address { top: 277px; }
  .contact__line--phones { top: 336px; word-spacing: 1px; }
  .contact__line--email { top: 396px; }
  .contact__line--mobile { top: 455px; }
  .contact__gap { display: inline-block; width: 36px; }
</style>
</head>
<body>
  <main class="canvas">
    <section class="card" aria-label="Pendrake Solicitors business card">
      <div class="card__rule card__rule--top"></div>
      <div class="card__backdrop" aria-hidden="true"></div>
      <div class="brand">
        <span class="brand__square" aria-hidden="true"></span>
        <span class="brand__name">Pendrake</span>
      </div>
      <address class="contact">
        <div class="contact__line contact__line--name">Darian Pendrake Principal Pendrake Solicitors Pty Ltd</div>
        <div class="contact__line contact__line--address">Level 6, 47 Corlett Street Melbourne VIC Australia 3000</div>
        <div class="contact__line contact__line--phones">T: +61 3 9555 0147<span class="contact__gap"></span>F: +61 3 9555 0162</div>
        <div class="contact__line contact__line--email">E: darian@pendrakesolicitors.com.au</div>
        <div class="contact__line contact__line--mobile">M:&nbsp; 0491 570 226</div>
      </address>
      <div class="card__rule card__rule--bottom"></div>
    </section>
  </main>
</body>
</html>
```